Kestrel - Transport company looking for a basic but smart design for the sides of our trailers

We have a logo 'Kestrel' which i would like to keep.
We have 2 companies Kestrel Haulage - Maroon signwriting (general freight ) and Kestrel Refrigerated - Blue signwriting (refrigerated freight) that can share the same design.
I'd like to come up with a basic modern design that will incorporate the Kestrel logo, the company name and the website and maybe an image at the front od some sort, a 3D swish or a stripe or something.
The Kestrel Haulage maroon trailers are too busy and I don't like the icicles on the front of the Kestrel Refrigerated blue trailers.

```html
<!DOCTYPE html>
<html lang="en">
<head>
<meta charset="utf-8">
<title>Kestrel Refrigerated – Trailer Side</title>
<link rel="stylesheet" href="https://fonts.googleapis.com/css2?family=Montserrat:wght@800;900&display=swap">
<style>
  :root {
    --maroon: #8a1c1e;
    --red-deep: #a5252a;
    --red: #c2333a;
    --red-bright: #d9454b;
    --paper: #ffffff;
  }
  html, body {
    margin: 0;
    padding: 0;
    overflow: hidden;
    background: var(--paper);
  }
  .trailer-side {
    position: relative;
    width: 1200px;
    height: 249px;
    overflow: hidden;
    background: var(--paper);
    font-family: "Montserrat", Arial, sans-serif;
  }
  .corner-graphic {
    position: absolute;
    inset: 0;
    width: 1200px;
    height: 249px;
  }
  .company {
    position: absolute;
    left: 199px;
    top: 15px;
    margin: 0;
    color: var(--maroon);
    line-height: 1;
  }
  .company-name {
    display: block;
    font-size: 16px;
    font-weight: 900;
    letter-spacing: 0.1px;
    text-transform: uppercase;
  }
  .company-web {
    display: block;
    margin-top: 3px;
    font-size: 13px;
    font-weight: 800;
  }
  .brand {
    position: absolute;
    left: 60px;
    top: 110px;
    display: flex;
    align-items: center;
    gap: 14px;
  }
  .brand-dot {
    width: 18px;
    height: 18px;
    border-radius: 50%;
    background: var(--maroon);
  }
  .brand-name {
    margin: 0;
    font-size: 54px;
    font-weight: 900;
    color: var(--maroon);
    text-transform: uppercase;
    line-height: 1;
    letter-spacing: 1px;
  }
</style>
</head>
<body>
  <div class="trailer-side">
    <svg class="corner-graphic" viewBox="0 0 1200 249" role="img" aria-label="Angular red swoosh graphic at the rear corner of the trailer">
      <defs>
        <linearGradient id="corner-fill" x1="0" y1="1" x2="1" y2="0">
          <stop offset="0" stop-color="var(--red-bright)"/>
          <stop offset="0.55" stop-color="var(--red)"/>
          <stop offset="1" stop-color="var(--red-deep)"/>
        </linearGradient>
      </defs>
      <polygon points="830,249 1100,0 1200,0 1200,249" fill="url(#corner-fill)"/>
    </svg>

    <p class="company">
      <span class="company-name">Kestrel Refrigerated</span>
      <span class="company-web">www.kestrelhaulage.com.au</span>
    </p>

    <div class="brand">
      <span class="brand-dot"></span>
      <p class="brand-name">Kestrel</p>
    </div>
  </div>
</body>
</html>
```